Bluecrest Learning Corps by graduating students from college in two years

Based on the logo design, create stationary and business cards for
Dr. Venrel T Oskamp, CEO, (703) 482-1736
and Marisa Deltoft, Respresentative, (301) 647-2208
Address: 4719 Pellham Court, Maplecrest Station, VA 22187
Incorporate elelments of the logo

Target Market(s)

USA

Font styles to use
Other font styles liked:
• match with the logo type style

```html
<!DOCTYPE html>
<html lang="en">
<head>
<meta charset="utf-8">
<title>Bluecrest Learning Corps – Business Cards</title>
<link href="https://fonts.googleapis.com/css2?family=Tinos:wght@400;700&display=swap" rel="stylesheet">
<style>
  :root {
    --gold: #f7c32e;
    --gold-text: #f2b31c;
    --navy: #1c2660;
    --ink: #222222;
    --paper: #ffffff;
    --backdrop: #e9e9ec;
  }
  * { box-sizing: border-box; margin: 0; padding: 0; }
  html, body { width: 1200px; height: 900px; overflow: hidden; }
  body {
    background: var(--backdrop);
    font-family: "Tinos", "Times New Roman", serif;
    display: flex;
    flex-direction: column;
    align-items: center;
    justify-content: center;
    gap: 50px;
  }
  .card {
    width: 630px;
    height: 360px;
    border-radius: 26px;
    position: relative;
    overflow: hidden;
    box-shadow: 0 6px 18px rgba(0,0,0,0.15);
  }
  /* Front */
  .card--front {
    background: var(--gold);
    display: flex;
    align-items: center;
    justify-content: center;
  }
  .brand {
    display: flex;
    align-items: center;
    gap: 14px;
    color: var(--navy);
    font-weight: 700;
    font-size: 34px;
    letter-spacing: 0.5px;
  }
  .brand__dot {
    width: 22px; height: 22px;
    border-radius: 50%;
    background: var(--navy);
    flex: none;
  }
  /* Back */
  .card--back { background: var(--paper); }
  .back__brand {
    position: absolute;
    left: 34px; top: 0; width: 240px; height: 300px;
    display: flex; align-items: center; justify-content: center;
  }
  .back__brand .brand { font-size: 21px; gap: 10px; }
  .back__brand .brand__dot { width: 16px; height: 16px; }
  .divider {
    position: absolute;
    left: 300px; top: 46px;
    width: 2px; height: 210px;
    background: var(--gold);
  }
  .contacts {
    position: absolute;
    left: 326px; top: 42px;
  }
  .person + .person { margin-top: 18px; }
  .person__name {
    color: var(--gold-text);
    font-weight: 700;
    font-size: 31px;
    line-height: 1.05;
  }
  .person__role {
    color: var(--ink);
    font-size: 17px;
    margin-top: 2px;
  }
  .person__phone {
    color: var(--ink);
    font-size: 17px;
    margin-top: 4px;
    display: flex; align-items: center; gap: 8px;
  }
  .icon { width: 14px; height: 14px; flex: none; }
  .address-band {
    position: absolute;
    left: 0; bottom: 0;
    width: 100%; height: 40px;
    background: var(--navy);
    color: var(--paper);
    font-size: 17px;
    display: flex; align-items: center;
    padding-left: 40px; gap: 8px;
  }
</style>
</head>
<body>
  <section class="card card--front" aria-label="Business card front">
    <div class="brand"><span class="brand__dot"></span>Bluecrest Learning Corps</div>
  </section>

  <section class="card card--back" aria-label="Business card back">
    <div class="back__brand">
      <div class="brand"><span class="brand__dot"></span>Bluecrest Learning Corps</div>
    </div>
    <div class="divider"></div>
    <div class="contacts">
      <div class="person">
        <div class="person__name">Dr. Venrel T Oskamp</div>
        <div class="person__role">CEO</div>
        <div class="person__phone">
          <svg class="icon" viewBox="0 0 24 24"><path fill="var(--gold)" d="M3 8c0-3 4-5 9-5s9 2 9 5v2h-5V8c-1-1-7-1-8 0v2H3z M6 12h12l2 9H4z"/></svg>
          (703) 482-1736
        </div>
      </div>
      <div class="person">
        <div class="person__name">Marisa Deltoft</div>
        <div class="person__role">Respresentative</div>
        <div class="person__phone">
          <svg class="icon" viewBox="0 0 24 24"><path fill="var(--gold)" d="M3 8c0-3 4-5 9-5s9 2 9 5v2h-5V8c-1-1-7-1-8 0v2H3z M6 12h12l2 9H4z"/></svg>
          (301) 647-2208
        </div>
      </div>
    </div>
    <div class="address-band">
      <svg class="icon" viewBox="0 0 24 24"><path fill="var(--paper)" d="M12 2a7 7 0 0 0-7 7c0 5 7 13 7 13s7-8 7-13a7 7 0 0 0-7-7zm0 10a3 3 0 1 1 0-6 3 3 0 0 1 0 6z"/></svg>
      4719 Pellham Court, Maplecrest Station, VA 22187
    </div>
  </section>
</body>
</html>
```